Web design project for exciting Australian start-up

Background
We are looking for a creative and talented web design artist to work alongside our market leading web developer.
• You will be required to create a modern and clean design theme for our website, incorporating selected rustic colour scheme elements for our exciting Australian start-up to operate within the coffee industry.
reoccurring work to be expected to flow to the successful designer.
Requirements
• c. 5 - 10 page website
• Landing page
• Log in/ out
• 404 template
• Typography is emphasised
• Please use either a) typemarrow.com, b) free web fonts, c) brindle fonts
• All design elements in vector format
• Preferably with icons for each header title(i.e. about us, how it works etc) but designer have free reign over how the site looks, so might not be applicable
• All pages to be responsive
• Down to eSlab resolution

High level visual design brief attached - additional pages to be worked from base design.

Design inspiration
• We would like to use design elements from the following sources:
http://www.zandrix.com/halcyon/ (Functionality)
Colour scheme refer to logo and complementary style guide

```html
<!DOCTYPE html>
<html lang="en">
<head>
<meta charset="utf-8">
<title>Brewline – Marketplace</title>
<link rel="stylesheet" href="https://fonts.googleapis.com/css2?family=Roboto:wght@300;400;500;700&display=swap">
<style>
:root{
  --orange:#ff9900;
  --orange-soft:#f5a443;
  --brown:#5a1e0f;
  --red:#8c1b17;
  --blue:#1f7fd6;
  --text:#222;
  --muted:#888;
  --line:#e3e3e3;
  --tab:#e6e6e6;
  --tab-dark:#d6d6d6;
  --star-off:#cfcfcf;
}
*{box-sizing:border-box;margin:0;padding:0}
html,body{width:1120px;height:1200px;overflow:hidden;background:#fff}
body{font-family:"Roboto",Arial,sans-serif;font-weight:300;color:var(--text);position:relative}
.top-rule{height:3px;background:var(--orange)}
.site-header{height:103px;position:relative}
.brand{position:absolute;left:39px;top:38px;display:flex;align-items:center;gap:10px;font-weight:700;font-size:22px;letter-spacing:2px;color:#1a1a1a}
.brand-dot{width:22px;height:22px;border-radius:50%;background:var(--orange)}
.account-nav{position:absolute;right:58px;top:24px;display:flex;align-items:center;gap:14px;font-size:13px;color:#555}
.avatar{width:35px;height:35px;border-radius:50%;background:linear-gradient(#777,#333)}
.account-nav .logout{color:var(--orange);text-decoration:underline}
.menu-icon{margin-left:8px;width:12px;display:flex;flex-direction:column;gap:3px}
.menu-icon span{height:2px;background:#222}
.hero{height:250px;position:relative;text-align:center;color:#fff;
  background:radial-gradient(circle at 55% 20%,#fbd6a1 0,#f4a74a 28%,transparent 45%),
  linear-gradient(100deg,#e88a2c 0%,#f7a64a 35%,#f3a045 60%,#e2852a 100%)}
.hero h1{font-weight:300;font-size:50px;padding-top:54px;letter-spacing:.5px}
.hero p{font-size:20px;line-height:24px;margin-top:2px}
.btn-outline{display:inline-block;margin-top:9px;border:2px solid #fff;border-radius:16px;font-size:16px;padding:3px 14px}
.search{position:absolute;left:826px;top:384px;width:246px;height:33px;border:1px solid #ccc;border-radius:17px;display:flex;align-items:center;overflow:hidden}
.search svg{margin-left:12px}
.search span{font-size:11px;font-style:italic;color:#999;margin-left:12px;flex:1}
.search b{background:var(--orange);color:#fff;font-weight:400;font-size:12px;height:100%;width:41px;display:flex;align-items:center;justify-content:center}
.results-bar{position:absolute;left:41px;top:454px;width:1039px;height:36px;border-bottom:1px solid var(--line);display:flex;align-items:center;font-size:14px}
.results-count{font-weight:400}
.query-chip{margin-left:16px;border:1px solid #ddd;height:25px;display:flex;align-items:center;color:#777;font-size:13px}
.query-chip .q{padding:0 20px 0 9px;border-right:1px solid #ddd;height:100%;display:flex;align-items:center}
.query-chip .star{width:24px;text-align:center;color:#ccc}
.controls{margin-left:auto;display:flex;align-items:center;gap:8px;color:#777;font-size:13px}
.select{border:1px solid #ddd;height:25px;display:flex;align-items:center;padding:0 8px;gap:8px}
.caret{width:0;height:0;border:5px solid transparent;border-top:6px solid var(--orange);margin-top:5px}
.pager{display:flex;align-items:center;gap:7px}
.pg-btn{width:15px;height:15px;background:var(--orange);color:#fff;font-size:11px;display:flex;align-items:center;justify-content:center;font-weight:700}
.pg-cur{border:1px solid #bbb;background:#eee;padding:0 3px;font-size:12px}
.filters{position:absolute;left:33px;top:496px;width:1040px;height:30px;font-size:13px;color:#444}
.tab{position:absolute;top:0;height:30px;display:flex;align-items:center;justify-content:center;padding-left:10px;background:var(--tab);
  clip-path:polygon(0 0,calc(100% - 10px) 0,100% 50%,calc(100% - 10px) 100%,0 100%,10px 50%)}
.tab.first{justify-content:flex-start;padding-left:13px;clip-path:polygon(0 0,calc(100% - 10px) 0,100% 50%,calc(100% - 10px) 100%,0 100%)}
.tab.dark{background:var(--tab-dark)}
.cards{position:absolute;left:52px;top:566px}
.card{position:absolute;width:242px;height:410px;border:1px solid var(--line)}
.card-logo{height:190px;display:flex;flex-direction:column;align-items:center;justify-content:center;position:relative;gap:8px}
.mark-square{width:70px;height:70px;background:var(--red)}
.mark-circle{width:70px;height:70px;border-radius:50%;background:var(--brown)}
.card-logo .name{font-size:24px;font-weight:700;color:var(--brown)}
.card-logo .name.red{color:#1a1a1a}
.zoom{position:absolute;left:76px;top:48px;width:84px;height:84px;border-radius:50%;background:rgba(255,165,40,.75);display:flex;align-items:center;justify-content:center}
.card-body{padding:0 13px 0 14px}
.tender{font-size:11px;color:var(--muted);display:flex;align-items:center;gap:5px;margin-top:8px}
.tender em{font-style:normal;color:var(--orange-soft)}
.badge{background:var(--blue);color:#fff;font-size:7.5px;font-weight:400;padding:1px 6px}
.card h3{font-size:13.2px;font-weight:400;line-height:19px;margin-top:3px;letter-spacing:-.1px;white-space:nowrap}
.spec{font-size:11.5px;color:var(--muted);margin-top:4px;line-height:14px}
.spec em{font-style:normal;color:var(--orange-soft)}
.help{display:inline-block;width:12px;height:12px;border-radius:50%;background:var(--orange);color:#fff;font-size:9px;text-align:center;line-height:12px;font-weight:700;margin-left:5px}
.stars{margin-top:8px;font-size:17px;letter-spacing:1px;color:var(--orange)}
.stars .off{color:var(--star-off)}
.perks{display:flex;gap:12px;margin-top:6px}
.btn-contact{display:inline-block;margin-top:12px;background:var(--orange);color:#fff;font-weight:500;font-size:12px;height:24px;line-height:24px;padding:0 13px}
</style>
</head>
<body>
<svg width="0" height="0" style="position:absolute">
  <defs>
    <g id="perk-icons" fill="#ff9900">
      <!-- delivery -->
      <path d="M1 2h3l2 7h6l1.5-5H5" fill="none" stroke="#ff9900" stroke-width="1.6" stroke-linejoin="round"/>
      <rect x="0" y="11" width="14" height="1.6"/>
      <!-- training cap -->
      <path d="M23 3l9 3.5-9 3.5-9-3.5z"/>
      <path d="M18 8.5v3c2 1.6 8 1.6 10 0v-3l-5 2z"/>
      <rect x="31" y="6.5" width="1.2" height="5"/>
      <!-- cup -->
      <path d="M40 2h8l-1 9.5h-6z"/>
      <rect x="39.5" y="1" width="9" height="1.8" rx=".5"/>
      <!-- promo -->
      <path d="M57 5h3l6-3.5v11L60 9h-3z"/>
      <rect x="58" y="9" width="2" height="3.5"/>
      <path d="M68 4.5q2 2.5 0 5M70.5 3q3.5 4 0 8" fill="none" stroke="#ff9900" stroke-width="1.2"/>
    </g>
  </defs>
</svg>

<div class="top-rule"></div>
<header class="site-header">
  <div class="brand">BREWLINE <span class="brand-dot"></span></div>
  <nav class="account-nav">
    <div class="avatar" role="img" aria-label="User profile photo"></div>
    <span>My Account</span><span>|</span>
    <span style="color:#333">Logged In</span><span>|</span>
    <span class="logout">Logout</span>
    <div class="menu-icon"><span></span><span></span><span></span></div>
  </nav>
</header>

<section class="hero" role="img" aria-label="Warm orange photo of a coffee cup, leaves and roasted beans">
  <h1>Marketplace</h1>
  <p>Search and Find the righ<br>Cofee Seller</p>
  <span class="btn-outline">Be a Seller</span>
</section>

<div class="search">
  <svg width="18" height="18" viewBox="0 0 18 18"><circle cx="7" cy="7" r="5.5" fill="none" stroke="#bbb" stroke-width="2"/><line x1="11" y1="11" x2="16" y2="16" stroke="#bbb" stroke-width="2.5"/></svg>
  <span>What are you lookin for?</span>
  <b>GO!</b>
</div>

<div class="results-bar">
  <span class="results-count">189 Results found for:</span>
  <div class="query-chip"><span class="q">[X]&nbsp;&nbsp;&nbsp;Café Morrow</span><span class="star">★</span></div>
  <div class="controls">
    <span style="margin-right:10px">Sort</span>
    <div class="select" style="width:133px;justify-content:space-between"><span>Highest rated</span><i class="caret"></i></div>
    <div class="select"><span>View</span>
      <svg width="15" height="15" viewBox="0 0 15 15" fill="#ff9900"><rect width="7" height="7"/><rect x="8" width="7" height="7"/><rect y="8" width="7" height="7"/><rect x="8" y="8" width="7" height="7"/></svg>
      <i class="caret"></i></div>
    <div class="pager" style="margin-left:10px"><span>Page</span><span class="pg-btn">‹</span><span class="pg-cur">1</span><span>2</span><span>3</span><span>4</span><span class="pg-btn">›</span></div>
  </div>
</div>

<div class="filters">
  <div class="tab first" style="left:0;width:120px;z-index:4">Tender format</div>
  <div class="tab" style="left:110px;width:86px;z-index:3">All</div>
  <div class="tab" style="left:186px;width:100px;z-index:2">One-off</div>
  <div class="tab" style="left:276px;width:120px;z-index:1">Recurring</div>
  <div class="tab dark first" style="left:786px;width:130px;padding-left:25px;z-index:2">Quantity (kg)</div>
  <div class="tab" style="left:906px;width:124px;z-index:1">35 kg/week</div>
</div>

<main class="cards">
  <article class="card" style="left:0;top:0">
    <div class="card-logo"><div class="mark-circle"></div><div class="name">Tamper Coffee</div>
      <div class="zoom"><svg width="40" height="40" viewBox="0 0 40 40"><circle cx="16" cy="16" r="11" fill="none" stroke="#fff" stroke-width="3"/><line x1="24" y1="24" x2="34" y2="34" stroke="#fff" stroke-width="3"/></svg></div></div>
    <div class="card-body">
      <div class="tender">Tender: <em>Coffe Bean XX</em><span class="badge">Top Rated</span></div>
      <h3>Providing the best coffe in Australia<br>Long Beach Coast.</h3>
      <div class="spec" style="margin-top:6px">Blend description: <em>Mix</em><span class="help">?</span></div>
      <div class="spec">Origin: <em>Colombia</em></div>
      <div class="spec">Grind Availability: <em>Granuñar, Powder...</em></div>
      <div class="stars">★★★<span class="off">★★</span></div>
      <div class="perks"><svg width="76" height="14" viewBox="0 0 76 14"><use href="#perk-icons"/></svg></div>
      <span class="btn-contact">CONTACT NOW</span>
    </div>
  </article>
  <article class="card" style="left:256px;top:0">
    <div class="card-logo"><div class="mark-square"></div><div class="name red">Harbor Roast</div></div>
    <div class="card-body">
      <div class="tender">Tender: <em>Coffe Bean XX</em><span class="badge">Premium</span></div>
      <h3>Providing the best coffe in Australia<br>Long Beach Coast.</h3>
      <div class="spec" style="margin-top:6px">Blend description: <em>Mix</em><span class="help">?</span></div>
      <div class="spec">Origin: <em>Colombia</em></div>
      <div class="spec">Grind Availability: <em>Granuñar, Powder...</em></div>
      <div class="stars">★★★<span class="off">★★</span></div>
      <div class="perks"><svg width="76" height="14" viewBox="0 0 76 14"><use href="#perk-icons"/></svg></div>
      <span class="btn-contact">CONTACT NOW</span>
    </div>
  </article>
  <article class="card" style="left:511px;top:0">
    <div class="card-logo"><div class="mark-circle"></div><div class="name">Tamper Coffee</div></div>
    <div class="card-body">
      <div class="tender">Tender: <em>Coffe Bean XX</em><span class="badge">Premium</span></div>
      <h3>Providing the best coffe in Australia<br>Long Beach Coast.</h3>
      <div class="spec" style="margin-top:6px">Blend description: <em>Mix</em><span class="help">?</span></div>
      <div class="spec">Origin: <em>Colombia</em></div>
      <div class="spec">Grind Availability: <em>Granuñar, Powder...</em></div>
      <div class="stars">★★★<span class="off">★★</span></div>
      <div class="perks"><svg width="76" height="14" viewBox="0 0 76 14"><use href="#perk-icons"/></svg></div>
      <span class="btn-contact">CONTACT NOW</span>
    </div>
  </article>
  <article class="card" style="left:767px;top:0">
    <div class="card-logo"><div class="mark-circle"></div><div class="name">Tamper Coffee</div></div>
    <div class="card-body">
      <div class="tender">Tender: <em>Coffe Bean XX</em><span class="badge">Premium</span></div>
      <h3>Providing the best coffe in Australia<br>Long Beach Coast.</h3>
      <div class="spec" style="margin-top:6px">Blend description: <em>Mix</em><span class="help">?</span></div>
      <div class="spec">Origin: <em>Colombia</em></div>
      <div class="spec">Grind Availability: <em>Granuñar, Powder...</em></div>
      <div class="stars">★★★<span class="off">★★</span></div>
      <div class="perks"><svg width="76" height="14" viewBox="0 0 76 14"><use href="#perk-icons"/></svg></div>
      <span class="btn-contact">CONTACT NOW</span>
    </div>
  </article>

  <article class="card" style="left:0;top:433px">
    <div class="card-logo"><div class="mark-circle"></div><div class="name">Tamper Coffee</div>
      <div class="zoom"><svg width="40" height="40" viewBox="0 0 40 40"><circle cx="16" cy="16" r="11" fill="none" stroke="#fff" stroke-width="3"/><line x1="24" y1="24" x2="34" y2="34" stroke="#fff" stroke-width="3"/></svg></div></div>
    <div class="card-body"><div class="tender">Tender: <em>Coffe Bean XX</em><span class="badge">Top Rated</span></div></div>
  </article>
  <article class="card" style="left:256px;top:433px">
    <div class="card-logo"><div class="mark-square"></div><div class="name red">Harbor Roast</div></div>
    <div class="card-body"><div class="tender">Tender: <em>Coffe Bean XX</em><span class="badge">Premium</span></div></div>
  </article>
  <article class="card" style="left:511px;top:433px">
    <div class="card-logo"><div class="mark-circle"></div><div class="name">Tamper Coffee</div></div>
    <div class="card-body"><div class="tender">Tender: <em>Coffe Bean XX</em><span class="badge">Premium</span></div></div>
  </article>
  <article class="card" style="left:767px;top:433px">
    <div class="card-logo"><div class="mark-circle"></div><div class="name">Tamper Coffee</div></div>
    <div class="card-body"><div class="tender">Tender: <em>Coffe Bean XX</em><span class="badge">Premium</span></div></div>
  </article>
</main>
</body>
</html>
```